Mark Tolvane actor business cards

I need unique and interesting business cards that have my headshot photo, my name, tagline/position/skills, contact info, preferred pronouns (he, him, his), and social media handles. These need to be memorable networking tools to hand out at events that stand out. I am an actor that works in theatre, film, and TV and usually play darker dramatic roles, though it doesn't have to necessarily need to be reflected in the design, but I am not a light, comedic actor. In my email tagline, My position/skills are "Actor, storyteller, theatre maker."

Target Market(s)

Casting directors, film and television community, theatre community.

Industry/Entity Type

Performing Art

Contact Information for Business Card

Mark Tolvane. Pronouns: he, him, his. Contact info: (555)-318-7064, Marktolvane.example, marktolvane@postbox.example. Talent representation: Kirwood Talent Agency. Social Media: Facebook page, twitter and instagram: @MarkTolvanePlays. Company Member of Harbin Theatre Company.

Font styles to use
Serif
Decorative

Colors

Designer to choose colors to be used in the design.

Requirements
Must have
• Headshot photo, name, tagline, preferred pronouns, contact info, Social media handle, talent agency logo, harbin theatre company logo. Both logos should be smaller than my name. Under or near Harbin logo, it should say "Company Member"
Nice to have
• I would like to have the photo, my name, tagline, and maybe pronouns on one side, and all contact info, and social media, and talent agency logo on the other. I would like the style to reflect my type which is a little more serious and somewhat darker, and definitely not comedic.
Should not have
• No extraneous theatre lights, camera, or film, etc. clip art or photos. Use solid backgrounds or photos provided.

```html
<!DOCTYPE html>
<html lang="en">
<head>
<meta charset="utf-8">
<title>Mark Tolvane – Business Cards</title>
<link rel="stylesheet" href="https://fonts.googleapis.com/css2?family=Cormorant+Garamond:ital,wght@0,600;1,500;1,600&family=Lato:wght@400;700&display=swap">
<style>
  :root {
    --stage: #3b3532;
    --card-light: #f4f4f4;
    --card-dark: #111111;
    --accent: #2b9ae8;
    --ink: #1a1a1a;
    --muted: #6a6a6a;
    --paper-text: #e9e9e9;
    --photo-top: #c9cdd6;
    --photo-bottom: #6a7cb6;
  }
  * { box-sizing: border-box; margin: 0; padding: 0; }
  html, body { width: 1200px; height: 900px; overflow: hidden; }
  body {
    background: var(--stage);
    font-family: "Lato", Arial, sans-serif;
    position: relative;
  }
  .card {
    position: absolute;
    width: 540px;
    height: 310px;
    top: 295px;
    overflow: hidden;
    box-shadow: 0 10px 30px rgba(0,0,0,.45);
  }
  /* ---------- shared agency mark ---------- */
  .agency-mark {
    position: absolute;
    display: flex;
    align-items: center;
    gap: 10px;
  }
  .agency-mark__dot {
    width: 14px; height: 14px; border-radius: 50%;
    background: var(--accent);
  }
  .agency-mark__name {
    font-family: "Cormorant Garamond", Georgia, serif;
    font-weight: 600;
    line-height: 1;
  }
  .agency-mark__sub { position: absolute; white-space: nowrap; }

  /* ---------- front ---------- */
  .card--front { left: 40px; background: var(--card-light); }
  .card--front .agency-mark { left: 34px; top: 44px; }
  .card--front .agency-mark__name { font-size: 40px; color: var(--ink); }
  .card--front .agency-mark__sub {
    left: 130px; top: 92px;
    font-size: 11px; color: var(--muted); letter-spacing: .5px;
  }
  .actor-name {
    position: absolute; left: 34px; top: 170px;
    font-family: "Cormorant Garamond", Georgia, serif;
    font-style: italic; font-weight: 600;
    font-size: 30px; line-height: 1.1; color: var(--accent);
  }
  .actor-skills {
    position: absolute; left: 34px; top: 209px;
    font-size: 14px; color: var(--ink);
  }
  .pronoun-band {
    position: absolute; left: 0; bottom: 0;
    width: 100%; height: 62px;
    background: var(--accent);
  }
  .pronouns {
    position: absolute; left: 34px; bottom: 12px;
    font-family: "Cormorant Garamond", Georgia, serif;
    font-style: italic; font-weight: 500;
    font-size: 34px; line-height: 1.1; color: #ffffff;
  }
  .headshot {
    position: absolute; right: 0; top: 0;
    width: 230px; height: 248px;
    background: linear-gradient(180deg, var(--photo-top) 0%, #a7b0cc 45%, var(--photo-bottom) 100%);
  }

  /* ---------- back ---------- */
  .card--back { left: 620px; background: var(--card-dark); }
  .card--back .agency-mark { left: 150px; top: 60px; }
  .card--back .agency-mark__name { font-size: 44px; color: #ffffff; }
  .card--back .agency-mark__sub {
    left: 290px; top: 112px;
    font-size: 12px; color: var(--paper-text);
  }
  .socials {
    position: absolute; right: 30px; top: 100px;
    display: flex; flex-direction: column; align-items: flex-end; gap: 6px;
  }
  .socials__icons { display: flex; gap: 5px; }
  .socials__icons span {
    width: 18px; height: 18px; border-radius: 50%; background: var(--accent);
  }
  .socials__handle { font-size: 11px; color: var(--paper-text); }
  .contact-list {
    position: absolute; left: 60px; top: 200px;
    list-style: none; display: flex; flex-direction: column; gap: 4px;
  }
  .contact-list li {
    display: flex; align-items: center; gap: 7px;
    font-size: 14px; color: var(--paper-text);
  }
  .contact-list svg { width: 12px; height: 12px; flex: none; }

  .company-member {
    position: absolute; right: 30px; bottom: 30px;
    display: flex; flex-direction: column; align-items: flex-end; gap: 3px;
  }
  .company-member__mark {
    display: flex; align-items: center; gap: 6px;
  }
  .company-member__square {
    width: 10px; height: 10px; background: var(--accent);
  }
  .company-member__name {
    font-family: "Cormorant Garamond", Georgia, serif;
    font-weight: 600; font-size: 17px; line-height: 1;
    color: #ffffff;
  }
  .company-member__label {
    font-size: 10px; letter-spacing: 1.5px; text-transform: uppercase;
    color: var(--paper-text);
  }
</style>
</head>
<body>

<section class="card card--front" aria-label="Card front">
  <div class="agency-mark">
    <span class="agency-mark__dot"></span>
    <span class="agency-mark__name">Kirwood</span>
  </div>
  <span class="agency-mark__sub">Talent Agency</span>

  <div class="headshot" role="img" aria-label="Headshot photo of Mark Tolvane"></div>

  <h1 class="actor-name">Mark Tolvane</h1>
  <p class="actor-skills">Actor, Storyteller, Theatre Maker</p>

  <div class="pronoun-band"></div>
  <p class="pronouns">He, Him, His</p>
</section>

<section class="card card--back" aria-label="Card back">
  <div class="agency-mark">
    <span class="agency-mark__dot"></span>
    <span class="agency-mark__name">Kirwood</span>
  </div>
  <span class="agency-mark__sub">Talent Agency</span>

  <div class="socials">
    <div class="socials__icons"><span></span><span></span><span></span></div>
    <span class="socials__handle">@MarkTolvanePlays</span>
  </div>

  <ul class="contact-list">
    <li>
      <svg viewBox="0 0 24 24" aria-hidden="true"><path fill="#2b9ae8" d="M6.6 10.8a15 15 0 0 0 6.6 6.6l2.2-2.2a1 1 0 0 1 1-.25 11.4 11.4 0 0 0 3.6.57 1 1 0 0 1 1 1V20a1 1 0 0 1-1 1A17 17 0 0 1 3 4a1 1 0 0 1 1-1h3.5a1 1 0 0 1 1 1c0 1.25.2 2.45.57 3.57a1 1 0 0 1-.25 1z"/></svg>
      (555)-318-7064
    </li>
    <li>
      <svg viewBox="0 0 24 24" aria-hidden="true"><path d="M2 5h20v14H2z M3 6l9 7 9-7" fill="none" stroke="#2b9ae8" stroke-width="2"/></svg>
      marktolvane@postbox.example
    </li>
    <li>
      <svg viewBox="0 0 24 24" aria-hidden="true"><circle cx="12" cy="12" r="9" fill="none" stroke="#2b9ae8" stroke-width="2"/><path d="M3 12h18M12 3c3 3 3 15 0 18M12 3c-3 3-3 15 0 18" fill="none" stroke="#2b9ae8" stroke-width="1.6"/></svg>
      www.Marktolvane.example
    </li>
  </ul>

  <div class="company-member">
    <div class="company-member__mark">
      <span class="company-member__square"></span>
      <span class="company-member__name">Harbin Theatre Company</span>
    </div>
    <span class="company-member__label">Company Member</span>
  </div>
</section>

</body>
</html>
```